Need Website Design for Non-Profit Veteran Site

I am looking for a very talented creative website designer for a modern feel. I'll give a little bit of guidance around what I am looking for and then your creative juices should kick in and design away. I have already purchased the domain but will need hosting (at least temporarily) and the creative design work done.The website domain is militarydocs.orgI am looking to attract current and veteran military providers (doctors, nurse practitioners, physician assistants, etc) to join and signup for membership. They would pay a yearly fee to join. Would need membership categories $135 for Provider, $55 Student, $100 for Retired, and Organization (Organization would be broken down into Less than 100 ($200), 100-249 ($250), 250-499 ($300), 500-999 ($400), 1,000-2,999 ($500), and 3,000 ($700). Would need Benefit built out and would need to accept money through CoinVane and other means. Since it's a new organization just starting, would also need a Donate button to get people to donate if they want any amount they would like. The second part of the website is that once they join, they will have acess to a list of all other providers who have registered within the website (not exportable) so they can connect with one another. If they want to see contact information this will be included in their fee as a benefit to socialize with one another. As part of the website, there will be another Veteran's portal so veterans who would like to connect with a provider around a particular speciality can reach out and request help from the doctor writing a nexus letter or letter to support the veteran who is filing a claim with the BQ. Veterans would pay a yearly sign-up fee of $30.00 and would need their membership benefits displayed. They would have access to a list of veterans in their region by state and distance, and can reach out to doctors to get their help. If a doctor and veteran agree, sharable inforamtion of medical hipaa documents can be exchanged via the website. The physician and veteran can negotiate a fee through the website only and share their details. This is a separate fee for this type of process between the provider and veteran. We will collect a $250 fee for admin on each of these and each project the veteran does with the provider will cost $450 (so essentially the doctor gets paid $450 and i get $250.00. This model could be changed over time as we start to test this out). A good example of 50% of what I'm looking for is something like the following website: https://www.lpkt.org/ It has some of the features but not all and my site should be more modernized to attract the veteran and military providers.

Target Market(s)

Current and retired military providers and veterans

Industry/Entity Type

Non Profit

Number of Pages Required

1 page

Requirements
Must have
• Military Design
• Modern Feel (Example templates for feel -https://quillmoth.com/free-photoshop-psd-web-design-template/)
• Donation box
• Stuff mentioned in the description)
Nice to have
• Open to feedback
Should not have
• Open to feedback

```html
<!DOCTYPE html>
<html lang="en">
<head>
<meta charset="utf-8">
<title>Harborwell Net</title>
<link href="https://fonts.googleapis.com/css2?family=PT+Serif:wght@700&family=Open+Sans:wght@400;600;700&display=swap" rel="stylesheet">
<style>
:root{
  --page:#545b45;
  --page-dark:#4a513c;
  --band:#3c4a1e;
  --ink:#111111;
  --white:#ffffff;
  --orange:#e99b1c;
  --red:#d8302f;
  --card:#3f4431;
  --card-text:#e6e6dc;
  --footer:#2c3222;
  --signup:#4f5c22;
}
*{margin:0;padding:0;box-sizing:border-box}
html,body{width:1200px;height:2719px;overflow:hidden}
body{position:relative;background:radial-gradient(ellipse at 30% 20%,var(--page) 0%,var(--page-dark) 100%);font-family:"Open Sans",Arial,sans-serif;color:var(--white)}
.abs{position:absolute}
.serif{font-family:"PT Serif",Georgia,serif;font-weight:700}

.top-band{left:580px;top:0;width:620px;height:40px;background:var(--band);clip-path:polygon(6% 0,100% 0,100% 100%,0 100%)}
.contact{right:100px;top:12px;font-size:12px;display:flex;gap:10px;align-items:center}
.contact svg{vertical-align:-2px;margin-right:5px}
.logo{left:100px;top:40px;font-size:38px}
.btn-join{left:872px;top:69px;width:98px;height:36px;border-radius:18px;background:var(--orange);font-size:13px;font-weight:700;display:flex;align-items:center;justify-content:center}
.btn-signup{left:979px;top:69px;width:121px;height:36px;border-radius:18px;border:2px solid #d8d8d0;font-size:13px;font-weight:700;display:flex;align-items:center;justify-content:center}

.nav{left:100px;top:127px;width:1000px;height:49px;background:var(--ink);display:flex;align-items:center;font-size:13px;font-weight:700}
.nav a{color:var(--white);text-decoration:none;flex:1;text-align:center}
.nav .donate{flex:0 0 163px;height:49px;background:var(--red);display:flex;align-items:center;justify-content:center;gap:6px}

.hero{left:100px;top:176px;width:1000px;height:459px;background:linear-gradient(100deg,#6d7a55 0%,#8a7a66 30%,#7d8a66 55%,#9b9580 75%,#5a6248 100%)}
.hero-title{left:185px;top:310px;font-size:50px}
.hero-text{left:185px;top:380px;width:440px;font-size:14px;line-height:24px}
.btn-more{left:185px;top:451px;width:132px;height:39px;border:2px solid var(--white);border-radius:20px;font-size:13px;font-weight:700;display:flex;align-items:center;justify-content:center}
.dot{width:12px;height:12px;border-radius:50%;background:var(--white);left:1046px}
.dot.ring{background:none;border:2px solid var(--white)}

.section-title{left:0;width:1200px;text-align:center;font-size:32px}

.card{top:789px;width:306px;height:359px;background:var(--card);text-align:center}
.card-img{position:absolute;left:16px;top:16px;width:274px;height:165px;border:3px solid var(--white)}
.card h3{position:absolute;top:206px;width:100%;font-size:18px;font-weight:600}
.card p{position:absolute;top:240px;left:4px;right:4px;font-size:11.5px;line-height:23px;color:var(--card-text);white-space:nowrap}
.card .more{position:absolute;top:322px;width:100%;font-size:12px;color:var(--orange);font-weight:600}

.about{left:100px;top:1231px;width:1000px;height:410px;background:linear-gradient(90deg,#b5bcb0 0%,#cfd3c8 45%,#b7c2cf 70%,#a9b6a4 100%)}
.about-frame{left:143px;top:1278px;width:916px;height:317px;border:2px solid rgba(255,255,255,.85)}
.about-title{left:100px;width:1000px;top:1343px;text-align:center;font-size:34px}
.about-sub{left:100px;width:1000px;top:1404px;text-align:center;font-size:16px;font-weight:600}

.event-side{top:1818px;height:327px;width:746px;left:158px;background:#c7cbb4;opacity:.85}
.event-side.right{left:905px;width:137px;background:#c2c6ae}
.event-main{left:296px;top:1802px;width:609px;height:357px;border:3px solid var(--orange);background:linear-gradient(100deg,#b88f86 0%,#c7b1a8 35%,#4c7c7a 70%,#1f3a40 100%)}
.event-shade{left:299px;top:1950px;width:603px;height:206px;background:linear-gradient(180deg,rgba(0,0,0,0) 0%,rgba(0,0,0,.55) 100%)}
.date-tag{left:551px;top:1791px;width:96px;height:100px;background:var(--orange);text-align:center}
.date-tag .m{display:block;margin-top:12px;font-size:24px}
.date-tag .d{display:block;font-size:30px;line-height:34px}
.event-title{left:296px;width:609px;top:2015px;text-align:center;font-size:19px;font-weight:700}
.event-text{left:360px;width:480px;top:2052px;text-align:center;font-size:13px;line-height:24px}

.signup{left:100px;top:2244px;width:1000px;height:117px;background:linear-gradient(90deg,var(--signup),#657030)}
.signup-text{left:149px;top:2268px;font-size:22px;line-height:34px;font-weight:600}
.signup-input{left:508px;top:2283px;width:417px;height:41px;background:var(--white);color:#888;font-size:13px;padding:12px 14px}
.signup-btn{left:925px;top:2283px;width:128px;height:41px;background:var(--red);font-size:20px;font-weight:700;display:flex;align-items:center;justify-content:center}

.footer{left:100px;top:2361px;width:1000px;height:266px;background:linear-gradient(180deg,#2f3524,var(--footer))}
.social{left:463px;top:2426px;display:flex;gap:6px}
.social span{width:50px;height:50px;border-radius:50%;border:2px solid var(--white)}
.foot-nav{left:100px;width:1000px;top:2504px;text-align:center;font-size:13px;font-weight:700}
.foot-nav span{margin:0 13px}
.foot-nav i{font-style:normal}
.copy{left:100px;width:1000px;top:2545px;text-align:center;font-size:11px}
</style>
</head>
<body>

<div class="abs top-band"></div>
<div class="abs contact">
  <span><svg width="12" height="12" viewBox="0 0 24 24"><path fill="#fff" d="M6.6 10.8a15 15 0 0 0 6.6 6.6l2.2-2.2c.3-.3.7-.4 1-.2 1.1.4 2.3.6 3.6.6.6 0 1 .4 1 1V20c0 .6-.4 1-1 1A17 17 0 0 1 3 4c0-.6.4-1 1-1h3.5c.6 0 1 .4 1 1 0 1.3.2 2.5.6 3.6.1.3 0 .7-.2 1z"/></svg>Call us : 1 800 555 0142</span>
  <span>|</span>
  <span><svg width="13" height="11" viewBox="0 0 24 18"><path fill="#fff" d="M0 0h24v2L12 10 0 2zM0 4.5l12 8 12-8V18H0z"/></svg>Email : info@harborwellnet.org</span>
</div>

<div class="abs logo serif">Harborwell Net</div>
<div class="abs btn-join">
  <svg width="12" height="12" viewBox="0 0 24 24" style="margin-right:6px"><circle cx="12" cy="7" r="5" fill="#fff"/><path fill="#fff" d="M2 24c0-6 4-10 10-10s10 4 10 10z"/></svg>JOIN</div>
<div class="abs btn-signup">
  <svg width="13" height="12" viewBox="0 0 24 24" style="margin-right:6px"><path fill="#fff" d="M2 10h12V5l8 7-8 7v-5H2z"/></svg>SIGN UP</div>

<nav class="abs nav">
  <a>HOME</a><a>ABOUT US</a><a>SERVICES</a><a>BENEFITS</a><a>TESTIMONIALS</a><a>CONTACT US</a>
  <a class="donate"><svg width="22" height="22" viewBox="0 0 24 24"><circle cx="14" cy="7" r="5" fill="none" stroke="#fff" stroke-width="1.6"/><path d="M2 16h5l4 2h6l4-3v2l-5 4H9l-7-2z" fill="none" stroke="#fff" stroke-width="1.6"/></svg>DONATE NOW</a>
</nav>

<div class="abs hero" role="img" aria-label="Smiling soldier in camouflage uniform standing before a row of national flags"></div>
<div class="abs hero-title serif">HARBORWELL NET</div>
<p class="abs hero-text">Nemo enim ipsam voluptatem quia voluptas sit aspernatur aut odit aut fugited quia consequuntur magni dolores eos qui.</p>
<div class="abs btn-more">READ MORE</div>
<div class="abs dot" style="top:357px"></div>
<div class="abs dot" style="top:384px"></div>
<div class="abs dot" style="top:411px"></div>
<div class="abs dot ring" style="top:438px"></div>

<h2 class="abs section-title serif" style="top:712px">OUR BENEFITS</h2>

<div class="abs card" style="left:116px">
  <div class="card-img" role="img" aria-label="Doctor taking notes with a patient at a desk" style="background:linear-gradient(120deg,#dfe8ee,#a9c3d6)"></div>
  <h3>COMMODI</h3>
  <p>Sed ut perspiciatis unde omnis iste natus error<br>sit voluptatem accusantium dolosaremque<br>laudantiusasaam rem aperiam,</p>
  <div class="more">READ MORE &#10148;</div>
</div>
<div class="abs card" style="left:448px">
  <div class="card-img" role="img" aria-label="Flag patch on a uniform sleeve" style="background:linear-gradient(120deg,#c0a080,#6a5f48)"></div>
  <h3>EXERCITATIONEM</h3>
  <p>Sed ut perspiciatis unde omnis iste natus error<br>sit voluptatem accusantium dolosaremque<br>laudantiusasaam rem aperiam,</p>
  <div class="more">READ MORE &#10148;</div>
</div>
<div class="abs card" style="left:780px">
  <div class="card-img" role="img" aria-label="Medical staff working at a computer in a pharmacy" style="background:linear-gradient(120deg,#b9c4cc,#e3e6ea)"></div>
  <h3>MAGNI DOLORES</h3>
  <p>Sed ut perspiciatis unde omnis iste natus error<br>sit voluptatem accusantium dolosaremque<br>laudantiusasaam rem aperiam,</p>
  <div class="more">READ MORE &#10148;</div>
</div>

<div class="abs about" role="img" aria-label="Nurse holding a clipboard in a bright hospital corridor"></div>
<div class="abs about-frame"></div>
<h2 class="abs about-title serif">ABOUT US</h2>
<p class="abs about-sub">Quis autem vel eum iure reprehenderitea voluptatesse</p>
<svg class="abs" style="left:569px;top:1452px" width="62" height="62" viewBox="0 0 62 62"><circle cx="31" cy="31" r="29" fill="none" stroke="#fff" stroke-width="3"/><path d="M24 18l20 13-20 13z" fill="#fff"/></svg>

<h2 class="abs section-title serif" style="top:1715px">LATEST EVENTS</h2>

<div class="abs event-side" role="img" aria-label="Previous event photo"></div>
<div class="abs event-side right" role="img" aria-label="Next event photo"></div>
<div class="abs event-main" role="img" aria-label="Caregiver assisting an elderly woman in a clinic"></div>
<div class="abs event-shade"></div>
<div class="abs date-tag serif"><span class="m">NOV</span><span class="d">10</span></div>
<div class="abs event-title">MAGNI DOLORES EOS</div>
<p class="abs event-text">Lorem ipsum dolor sit amet, consectetur adipiscing elit, sed do eiusmod tempor incididunt ut labore et dolore magna aliqua.</p>
<svg class="abs" style="left:94px;top:1964px" width="36" height="68" viewBox="0 0 36 68"><path d="M34 2L2 34l32 32" fill="none" stroke="#fff" stroke-width="2"/></svg>
<svg class="abs" style="left:1070px;top:1964px" width="36" height="68" viewBox="0 0 36 68"><path d="M2 2l32 32L2 66" fill="none" stroke="#fff" stroke-width="2"/></svg>

<div class="abs signup"></div>
<p class="abs signup-text">Veterans would pay a yearly fee<br>of $30.00 to sign-up</p>
<div class="abs signup-input">Enter Email</div>
<div class="abs signup-btn">SIGN UP</div>

<div class="abs footer"></div>
<div class="abs social" aria-label="Social links"><span></span><span></span><span></span><span></span><span></span></div>
<div class="abs foot-nav">
  <span>HOME</span><i>|</i><span>ABOUT US</span><i>|</i><span>SERVICES</span><i>|</i><span>BENEFITS</span><i>|</i><span>TESTIMONIALS</span><i>|</i><span>CONTACT US</span>
</div>
<p class="abs copy">&copy; Copyright 2018 Harborwell Net.All Rights Reserved &nbsp;|&nbsp; Terms of Use &nbsp;|&nbsp; Privacy Policy</p>

</body>
</html>
```